Birchline Septic Solutions

Would like to see some single sided ones but would also like to see some double sided with one sided only being the logo. Owners name is Colin Vandro. Phone number is 555-214-0387
Services are pumping, inspections, installs, and repairs

Contact Information for Business Card

555-241-0387 Colin Vandro Ashford Glen, OH

```html
<!DOCTYPE html>
<html lang="en">
<head>
<meta charset="utf-8">
<title>Birchline Septic Solutions – Business Card</title>
<link href="https://fonts.googleapis.com/css2?family=Lato:wght@400;700;900&display=swap" rel="stylesheet">
<style>
  :root {
    --stage: #2b2b2b;
    --card-black: #050505;
    --card-white: #ffffff;
    --teal: #2bbcb6;
    --ink: #141414;
    --silver: #e6e6e6;
    --pipe-light: #f4f4f4;
    --pipe-mid: #d4d4d4;
  }
  * { margin: 0; padding: 0; box-sizing: border-box; }
  html, body {
    width: 1200px;
    height: 875px;
    overflow: hidden;
    background: var(--stage);
    font-family: "Lato", Arial, sans-serif;
  }
  .sheet {
    width: 1200px;
    height: 875px;
    display: flex;
    flex-direction: column;
    align-items: center;
    justify-content: center;
    gap: 50px;
  }
  .card {
    position: relative;
    width: 620px;
    height: 354px;
    border-radius: 18px;
    overflow: hidden;
  }

  /* Front side */
  .card-front { background: var(--card-black); }
  .card-front .accent-band {
    position: absolute;
    inset: 0;
    width: 100%;
    height: 100%;
  }
  .brand {
    position: absolute;
    left: 0;
    right: 0;
    top: 70px;
    display: flex;
    align-items: center;
    justify-content: center;
    gap: 16px;
  }
  .brand-mark {
    width: 22px;
    height: 22px;
    background: var(--teal);
  }
  .brand-name {
    color: var(--silver);
    font-weight: 900;
    font-size: 34px;
    letter-spacing: 3px;
    text-transform: uppercase;
    line-height: 1.15;
  }
  .services {
    position: absolute;
    left: 28px;
    bottom: 30px;
    color: var(--teal);
    font-weight: 700;
    font-size: 17px;
    letter-spacing: 0.6px;
    text-transform: uppercase;
    transform: rotate(-9deg);
    transform-origin: left bottom;
  }

  /* Back side */
  .card-back { background: var(--card-white); }
  .pipe-artwork {
    position: absolute;
    inset: 0;
    background:
      radial-gradient(ellipse at 50% 32%, var(--card-white) 0%, rgba(255,255,255,0.9) 32%, rgba(255,255,255,0) 60%),
      linear-gradient(135deg, var(--pipe-light) 0%, var(--pipe-mid) 45%, var(--pipe-light) 70%, var(--pipe-mid) 100%);
  }
  .contact {
    position: absolute;
    left: 0;
    right: 0;
    top: 92px;
    text-align: center;
  }
  .contact-name {
    color: var(--teal);
    font-weight: 700;
    font-size: 50px;
    letter-spacing: 1px;
    text-transform: uppercase;
    line-height: 1;
  }
  .contact-phone {
    margin-top: 8px;
    color: var(--ink);
    font-weight: 400;
    font-size: 30px;
    letter-spacing: 9px;
  }
  .contact-location {
    margin-top: 6px;
    display: inline-flex;
    align-items: center;
    gap: 10px;
    color: var(--ink);
    font-size: 13px;
    letter-spacing: 1px;
    text-transform: uppercase;
  }
  .contact-location .rule {
    width: 90px;
    height: 2px;
    background: var(--teal);
  }
</style>
</head>
<body>
  <main class="sheet">
    <section class="card card-front" aria-label="Business card front">
      <svg class="accent-band" viewBox="0 0 620 354" preserveAspectRatio="none" aria-hidden="true">
        <polygon points="0,300 620,190 620,354 0,354" fill="#ffffff"/>
        <polygon points="520,208 620,190 620,232 560,232" fill="#2bbcb6"/>
      </svg>
      <div class="brand">
        <span class="brand-mark" aria-hidden="true"></span>
        <span class="brand-name">Birchline<br>Septic Solutions</span>
      </div>
      <p class="services">Pumping, Inspections, Installs &amp; Repairs</p>
    </section>

    <section class="card card-back" aria-label="Business card back">
      <div class="pipe-artwork" role="img" aria-label="Silver plumbing pipes with valves and gauges spread across the card"></div>
      <div class="contact">
        <p class="contact-name">Colin Vandro</p>
        <p class="contact-phone">555-241-0387</p>
        <p class="contact-location"><span class="rule"></span>Ashford Glen, OH<span class="rule"></span></p>
      </div>
    </section>
  </main>
</body>
</html>
```